Business Cards for new orthopaedic surgery practice

My husband and I are starting our own orthopaedic surgery practice. We are looking for a business card that is uniform, but one will have my name/title and the other will have his. You can just create one design with my name on it for now. But when I choose your design as the winning design I will ask that you add another copy with his name/title.

We are looking for classy, simple, elite all in one. We like dark blues/a little gold/yellow. Something that goes with our logo. We want our logo incorporated. Here is all the info you need:
Business name: RV Bone & Vitality Center
Location: 38517 North Willowmere Ave
Larkmoor Springs, FL 33490
Phone: 954-218-4063
Fax: 954-582-7341
Email: info@myrvbonecare.example

Names: Lydia Vance, M.D.
Board Certified Hand and Upper Extremity Surgeon

Ebo Dansu, M.D.
Board Certified Hip & Knee Replacement/General Orthopaedic Surgeon

Can decide what you want to put on the back. Maybe a slogan:
Grounded in Care. Centered on You

I am just going to upload our logo. The only thing is if we select you as the winning design, the location, and phone numbers may change. We will need your help to update that once fully solidified.

Industry/Entity Type

Medical

Contact Information for Business Card

Colors
0054AA
0677BA
7BADD7
CADEEF
E8F1F8
0094D4
00A9DD
6FCCEA
C7EBF8
E9F6FB

Requirements
Must have
• class, appeal,
Should not have
• We want to air on the side of masculine if we are looking at masculine vs. feminine feel. But we still want it classy, sophisticated, and something we will love

```html
<!DOCTYPE html>
<html lang="en">
<head>
<meta charset="utf-8">
<title>RV Bone &amp; Vitality Center – Business Card</title>
<link rel="stylesheet" href="https://fonts.googleapis.com/css2?family=Montserrat:wght@400;500;700&display=swap">
<style>
  :root {
    --navy: #1b2a5e;
    --navy-deep: #14204c;
    --navy-pattern: #22357a;
    --gold: #c9a24a;
    --white: #ffffff;
    --stage: #1c1c1f;
  }
  * { margin: 0; padding: 0; box-sizing: border-box; }
  html, body { width: 1200px; height: 900px; overflow: hidden; }
  body {
    background: var(--stage);
    font-family: "Montserrat", Arial, sans-serif;
    position: relative;
  }
  .card {
    position: absolute;
    left: 285px;
    width: 630px;
    height: 360px;
    border-radius: 28px;
    overflow: hidden;
  }
  .card--front { top: 70px; background: var(--white); }
  .card--back { top: 470px; background: var(--navy); }

  /* front */
  .brand {
    position: absolute; left: 48px; top: 36px;
    display: flex; align-items: center; gap: 12px;
    color: var(--navy); font-weight: 700; font-size: 16px; line-height: 1.3;
    width: 250px;
  }
  .brand__dot {
    flex: none; width: 34px; height: 34px; border-radius: 50%;
    background: var(--navy);
  }
  .contact {
    position: absolute; left: 48px; top: 150px;
    list-style: none; color: var(--navy); font-size: 14px; line-height: 1.6;
  }
  .contact li { display: flex; align-items: center; gap: 9px; white-space: nowrap; }
  .contact svg { width: 13px; height: 13px; flex: none; }
  .contact .accent { color: var(--gold); }
  .person {
    position: absolute; right: 44px; top: 108px; text-align: right;
  }
  .person__name {
    color: var(--gold); font-weight: 700; font-size: 25px;
    letter-spacing: 2px; text-transform: uppercase; white-space: nowrap;
  }
  .person__title {
    color: var(--navy); font-size: 14.5px; line-height: 1.35; margin-top: 4px;
  }
  .address {
    position: absolute; right: 44px; top: 232px; text-align: right;
    color: var(--navy); font-size: 14.5px; line-height: 1.35; font-style: normal;
  }
  .slogan-band {
    position: absolute; left: 0; right: 0; bottom: 0; height: 42px;
    background: var(--navy-deep);
    display: flex; align-items: center; padding-left: 48px;
  }
  .slogan-band__text {
    color: var(--gold); font-size: 15px; font-weight: 500;
  }

  /* back */
  .back-pattern {
    position: absolute; inset: 0;
    background: linear-gradient(135deg, var(--navy) 0%, var(--navy-pattern) 50%, var(--navy) 100%);
  }
  .back-mark {
    position: absolute; left: 50%; top: 50%; transform: translate(-50%, -50%);
    display: flex; align-items: center; gap: 12px;
    color: var(--white); font-weight: 700; font-size: 19px; white-space: nowrap;
  }
  .back-mark__dot {
    width: 30px; height: 30px; border-radius: 50%; border: 2px solid var(--gold);
  }
</style>
</head>
<body>

<section class="card card--front" aria-label="Business card front">
  <div class="brand">
    <span class="brand__dot"></span>
    <span>RV Bone &amp; Vitality Center</span>
  </div>

  <ul class="contact">
    <li>
      <svg viewBox="0 0 16 16" aria-hidden="true"><path fill="#c9a24a" d="M3.6 1.5l2.3 2.6-1.3 1.8c.9 2 2.5 3.6 4.5 4.5l1.8-1.3 2.6 2.3-1.3 2.4C7 13.4 2.6 9 1.2 2.8z"/></svg>
      954-218-4063
    </li>
    <li>
      <svg viewBox="0 0 16 16" aria-hidden="true"><path fill="none" stroke="#c9a24a" stroke-width="1.4" d="M4 6V2h8v4M2.5 6h11v6h-11zM5 10h6v4H5z"/></svg>
      954-582-7341
    </li>
    <li>
      <svg viewBox="0 0 16 16" aria-hidden="true"><path fill="none" stroke="#c9a24a" stroke-width="1.4" d="M1.5 3.5h13v9h-13zM1.5 3.5L8 9l6.5-5.5"/></svg>
      info@myrvbonecare.example
    </li>
    <li>
      <svg viewBox="0 0 16 16" aria-hidden="true"><g fill="none" stroke="#c9a24a" stroke-width="1.3"><circle cx="8" cy="8" r="6.3"/><path d="M1.7 8h12.6M8 1.7c-3 3.4-3 9.2 0 12.6M8 1.7c3 3.4 3 9.2 0 12.6"/></g></svg>
      <span>www.<span class="accent">myrvbonecare</span>.example</span>
    </li>
  </ul>

  <div class="person">
    <h1 class="person__name">Lydia Vance, M.D</h1>
    <p class="person__title">Board Certified Hand and<br>Upper Extremity Surgeon</p>
  </div>

  <address class="address">
    38517 North Willowmere<br>Ave Larkmoor Springs,<br>FL 33490
  </address>

  <div class="slogan-band">
    <span class="slogan-band__text">Grounded in Care. Centered on You</span>
  </div>
</section>

<section class="card card--back" aria-label="Business card back">
  <div class="back-pattern" role="img" aria-label="Tone-on-tone repeating practice mark pattern in navy"></div>
  <div class="back-mark">
    <span class="back-mark__dot"></span>
    <span>RV Bone &amp; Vitality Center</span>
  </div>
</section>

</body>
</html>
```